Dew and Willow med spa needs an awesome eye catching billboard ad

We need a billboard ad design for a Med Spa with location sin Fernbrook and Windermere FL A medical spa where the beauty of nature meets the power of science to treat the whole person, mind, body and soul.

Marigold Radiance Med Spa is a medical spa where the beauty of nature meets the power of science to create gorgeous, youthful looking skin. Located in Fernbrook, Florida, but also serving Four Corners, Celebration, and Windermere, Florida, the talented professional team brings decades of experience in world-class skin care to provide holistic, science-backed aesthetic services and health coaching.

Industry/Entity Type

Spa

Colors
fbee3e
fece3e
eea4c8
e667a6
fbee3d

Requirements
Must have
• Locations in Fernbrook and Lakeview Park
Phone 407-555-0148
website www.dewandwillow-example.com

Boards for each:
Aesthetic Treatments
Cosmetic Injectables
Quoria facial
add color vs too many earthtones, to catch the eye perhaps using yellow, something that catches the eye and stands out from the normal everyday
Thank you!!!!
Nice to have
• Boards for each:
Aesthetic Treatments
Cosmetic Injectables
Quoria facial
add color vs too many earthtones, to catch the eye
photos that match services,
Thank you!!!!

```html
<!DOCTYPE html>
<html lang="en">
<head>
<meta charset="utf-8">
<title>Marigold Radiance Med Spa – Quoria Facial Billboard</title>
<link rel="stylesheet" href="https://fonts.googleapis.com/css2?family=Crimson+Text:wght@400;700&family=Marcellus&display=swap">
<style>
  :root {
    --stage: #4d4d4d;
    --sun-yellow: #fbee3d;
    --marigold: #fece3e;
    --amber: #f7941d;
    --pale-yellow: #fff37e;
    --rose: #e667a6;
    --white: #ffffff;
    --ink: #161616;
    --gold-taupe: #b9a27a;
    --photo-light: #eceae8;
    --photo-mid: #c9bdb3;
  }
  * { margin: 0; padding: 0; box-sizing: border-box; }
  html, body {
    width: 857px;
    height: 1200px;
    overflow: hidden;
    background: var(--stage);
  }
  .billboard {
    position: absolute;
    left: 28px;
    top: 400px;
    width: 800px;
    height: 400px;
    box-shadow: 0 6px 18px rgba(0, 0, 0, 0.45);
  }
  .billboard svg { display: block; width: 800px; height: 400px; }
  .brand-name {
    font-family: "Crimson Text", serif;
    font-weight: 400;
    fill: var(--gold-taupe);
  }
  .headline {
    font-family: "Crimson Text", serif;
    font-weight: 700;
    font-size: 50px;
    fill: var(--sun-yellow);
    letter-spacing: 1px;
  }
  .phone {
    font-family: "Marcellus", serif;
    font-size: 42px;
    fill: var(--ink);
    letter-spacing: 1px;
    stroke: var(--ink);
    stroke-width: 0.6px;
  }
  .website {
    font-family: "Crimson Text", serif;
    font-size: 19px;
    fill: var(--ink);
    letter-spacing: 0.5px;
  }
  .locations {
    font-family: "Crimson Text", serif;
    font-size: 18px;
    fill: var(--ink);
  }
</style>
</head>
<body>
  <main class="billboard">
    <svg viewBox="0 0 800 400" xmlns="http://www.w3.org/2000/svg">
      <defs>
        <linearGradient id="base-glow" x1="0" y1="0" x2="0" y2="1">
          <stop offset="0" stop-color="var(--marigold)"/>
          <stop offset="1" stop-color="var(--sun-yellow)"/>
        </linearGradient>
        <linearGradient id="sun-ring" x1="0" y1="0" x2="0" y2="1">
          <stop offset="0" stop-color="var(--amber)"/>
          <stop offset="0.55" stop-color="var(--marigold)"/>
          <stop offset="1" stop-color="var(--sun-yellow)"/>
        </linearGradient>
        <linearGradient id="accent-dot" x1="0" y1="0" x2="1" y2="1">
          <stop offset="0" stop-color="var(--amber)"/>
          <stop offset="1" stop-color="var(--sun-yellow)"/>
        </linearGradient>
        <linearGradient id="photo-tone" x1="0" y1="0" x2="1" y2="1">
          <stop offset="0" stop-color="var(--photo-light)"/>
          <stop offset="1" stop-color="var(--photo-mid)"/>
        </linearGradient>
      </defs>

      <!-- base -->
      <rect class="base" width="800" height="400" fill="url(#base-glow)"/>

      <!-- right information panel -->
      <rect class="info-panel" x="420" y="0" width="380" height="349" fill="var(--white)"/>
      <rect class="headline-band" x="420" y="121" width="380" height="132" fill="var(--rose)"/>
      <rect class="locations-band" x="420" y="349" width="380" height="51" fill="var(--marigold)"/>

      <!-- circular frame -->
      <circle class="sun-ring" cx="190" cy="200" r="262" fill="url(#sun-ring)"/>
      <circle class="inner-ring" cx="190" cy="200" r="232" fill="var(--pale-yellow)"/>
      <circle class="ring-line" cx="190" cy="200" r="222" fill="none" stroke="var(--white)" stroke-width="1.5"/>
      <circle class="treatment-photo" cx="190" cy="200" r="212" fill="url(#photo-tone)"
              role="img" aria-label="Photo of a client receiving a facial treatment from a gloved aesthetician"/>

      <!-- accent dots -->
      <circle class="accent-dot" cx="412" cy="65" r="13" fill="url(#accent-dot)"/>
      <circle class="accent-dot" cx="432" cy="257" r="12" fill="url(#accent-dot)"/>
      <circle class="accent-dot" cx="387" cy="336" r="29" fill="url(#accent-dot)"/>

      <!-- brand -->
      <circle class="brand-mark" cx="474" cy="64" r="18" fill="var(--gold-taupe)"/>
      <text class="brand-name" x="505" y="64" font-size="23" letter-spacing="2.5">MARIGOLD RADIANCE</text>
      <text class="brand-name" x="506" y="86" font-size="12" letter-spacing="4">MED SPA</text>

      <!-- headline -->
      <text class="headline" x="610" y="178" text-anchor="middle">QUORIA</text>
      <text class="headline" x="610" y="232" text-anchor="middle">FACIAL</text>

      <!-- contact -->
      <text class="phone" x="610" y="300" text-anchor="middle">407-555-0148</text>
      <text class="website" x="610" y="331" text-anchor="middle">www.DewAndWillow-example.com</text>

      <!-- locations -->
      <text class="locations" x="608" y="381" text-anchor="middle">Locations in Fernbrook and Lakeview Park</text>
    </svg>
  </main>
</body>
</html>
```